Business Card Design Project

We have recently completed CraftHive projects for a new logo and wesbite.
We now require new business cards.
We hand out very little printed material to clients as all information is online. When we do hand out something, like a business card, we want it to have real impact and make a statement about the quality and professionalism of our company.
We have an idea of what we want our card to look like but we want a designer to make sure they have impact and look great.
Our requirements are…
Size: 85mm X 55mm - Landscape
Front of card: Logo plus the following contact information.
Dennis Marlow
Operations Manager
Phone +44(0) 1632 xxx xxx
Mobile +44(0) 7700 xxx xxx
Email denmo@korvantix.example
Address 17 Pellick Row, Aberdeen AB12 9QZ
Website www.korvantix.example
How you layout the front of the card is up to you, we would like to see some different ideas. Attached are two versions of our logo that may be used.
Back of card: We would like this to be simple but again have impact. Our current thought is to have the logo or just the large W design from the logo in white against a dark background, perhaps made up from the dark green in the logo.
The logos are attached so you can see the colours in them but the dark ones are..
Dark Blue = C:88, M:55, Y:44, K:28
Dark Green = C:87, M:53, Y:50, K:50
We sometimes also use a bright orange as an accent or highlight colour…
Orange: = C:0, M:39, Y:94, K:0

```html
<!DOCTYPE html>
<html lang="en">
<head>
<meta charset="utf-8">
<title>Korvantix Business Cards</title>
<link href="https://fonts.googleapis.com/css2?family=Open+Sans:wght@400;600;700;800&display=swap" rel="stylesheet">
<style>
  :root {
    --ink-teal: #22434a;
    --ink-text: #2c4a52;
    --body-text: #3a3f42;
    --moss: #7c9360;
    --paper: #ffffff;
    --stage: #e9e7e3;
  }
  * { margin: 0; padding: 0; box-sizing: border-box; }
  html, body { width: 1200px; height: 800px; overflow: hidden; }
  body {
    background: var(--stage);
    font-family: "Open Sans", sans-serif;
    position: relative;
  }
  .card {
    position: absolute;
    width: 501px;
    height: 324px;
    border-radius: 14px;
    overflow: hidden;
    box-shadow: 0 3px 8px rgba(0,0,0,0.18);
  }
  .card--front { left: 85px; top: 65px; background: var(--paper); }
  .card--back-dark { left: 610px; top: 67px; background: var(--ink-teal); }
  .card--back-gradient { left: 86px; top: 408px; background: linear-gradient(90deg, var(--ink-teal) 0%, #4f6a53 50%, var(--moss) 100%); }
  .card--back-light { left: 611px; top: 408px; background: var(--paper); }

  .brand {
    position: absolute;
    left: 38px;
    top: 160px;
    width: 210px;
    text-align: center;
    font-weight: 800;
    font-size: 33px;
    letter-spacing: 0.5px;
    color: var(--ink-text);
  }
  .divider {
    position: absolute;
    left: 265px;
    top: 72px;
    width: 2px;
    height: 160px;
    background: linear-gradient(180deg, rgba(44,74,82,0) 0%, rgba(44,74,82,0.55) 50%, rgba(44,74,82,0) 100%);
  }
  .contact { position: absolute; left: 293px; top: 70px; color: var(--body-text); }
  .contact__name { font-weight: 700; font-size: 17px; color: var(--ink-text); line-height: 20px; }
  .contact__role { font-size: 12.5px; line-height: 18px; margin-bottom: 18px; }
  .contact__list { list-style: none; font-size: 12.5px; line-height: 18.5px; }
  .contact__list li { display: flex; align-items: center; gap: 5px; }
  .contact__list svg { width: 10px; height: 10px; flex: none; }
  .contact__address { margin-top: 17px; font-size: 12.5px; line-height: 18.5px; padding-left: 2px; }

  .back-mark {
    position: absolute;
    left: 0; right: 0;
    top: 95px;
    display: flex;
    justify-content: center;
    align-items: center;
    gap: 14px;
    font-weight: 700;
    font-size: 46px;
    letter-spacing: 1px;
  }
  .back-mark__dot { width: 22px; height: 22px; border-radius: 50%; background: currentColor; }
  .back-url {
    position: absolute;
    left: 0; right: 0;
    top: 266px;
    text-align: center;
    font-size: 15px;
    letter-spacing: 2.6px;
  }
  .on-dark { color: var(--paper); }
  .on-light { color: var(--ink-text); }
  .card--back-gradient .back-url { top: 266px; }
</style>
</head>
<body>

<section class="card card--front">
  <div class="brand">KORVANTIX</div>
  <div class="divider"></div>
  <div class="contact">
    <p class="contact__name">DENNIS MARLOW</p>
    <p class="contact__role">Operations Manager</p>
    <ul class="contact__list">
      <li>
        <svg viewBox="0 0 10 10" aria-hidden="true"><circle cx="5" cy="5" r="4.4" fill="none" stroke="#3a3f42" stroke-width="0.9"/><path d="M3.3 2.6c-.4.6.1 2.6 1.8 3.9 1.2.9 1.9.8 2.2.4l-.8-.9-.6.3c-.6-.3-1.2-.9-1.5-1.5l.3-.6z" fill="#3a3f42"/></svg>
        +44(0) 1632 xxx xxx
      </li>
      <li>
        <svg viewBox="0 0 10 10" aria-hidden="true"><rect x="2.6" y="0.6" width="4.8" height="8.8" rx="0.8" fill="none" stroke="#3a3f42" stroke-width="1"/><circle cx="5" cy="7.8" r="0.6" fill="#3a3f42"/></svg>
        +44(0) 7700 xxx xxx
      </li>
      <li>
        <svg viewBox="0 0 10 10" aria-hidden="true"><rect x="0.6" y="2" width="8.8" height="6.2" fill="#3a3f42"/><path d="M0.8 2.3 5 5.6 9.2 2.3" fill="none" stroke="#fff" stroke-width="0.8"/></svg>
        denmo@korvantix.example
      </li>
      <li>
        <svg viewBox="0 0 10 10" aria-hidden="true"><g fill="none" stroke="#3a3f42" stroke-width="0.8"><circle cx="5" cy="5" r="4.3"/><ellipse cx="5" cy="5" rx="1.9" ry="4.3"/><path d="M0.7 5h8.6M1.4 2.9h7.2M1.4 7.1h7.2"/></g></svg>
        www.korvantix.example
      </li>
    </ul>
    <p class="contact__address">17 Pellick Row,<br>Aberdeen AB12 9QZ</p>
  </div>
</section>

<section class="card card--back-dark">
  <div class="back-mark on-dark"><span class="back-mark__dot"></span>KORVANTIX</div>
  <p class="back-url on-dark">www.korvantix.example</p>
</section>

<section class="card card--back-gradient">
  <div class="back-mark on-dark"><span class="back-mark__dot"></span>KORVANTIX</div>
  <p class="back-url on-dark">www.korvantix.example</p>
</section>

<section class="card card--back-light">
  <div class="back-mark on-light"><span class="back-mark__dot"></span>KORVANTIX</div>
  <p class="back-url on-light">www.korvantix.example</p>
</section>

</body>
</html>
```